Healthcare and Professional IT Services Company need a redesigned business card

We are a IT Services company that targets small medical practices and professional business such as Attorneys, Accounts, Architects etc. We want to communicate a professional yet friendly image using recent logo redesign here on ArtHarbor. Like to see the colors blue and orange in the design. Must use the Tall Pine Computing as displayed in the new logo - then also want to incorporate the fish logo as well.

Target Market(s)

Small medical and professional services

Industry/Entity Type

It Company

Contact Information for Business Card

The usual stuff, place for name address phone website. Also maybe our tagline which is "hooked on technology"

Requirements
Must have
• My new logo and the fish somewhere on the card

```html
<!DOCTYPE html>
<html lang="en">
<head>
<meta charset="utf-8">
<title>Tall Pine Computing – Business Card</title>
<link href="https://fonts.googleapis.com/css2?family=Arimo:wght@400;700&family=Playfair+Display:wght@700&display=swap" rel="stylesheet">
<style>
  :root{
    --page:#e9ebee;
    --card-white:#fbfbfc;
    --blue-light:#5fd0ef;
    --blue-mid:#2eaee0;
    --blue-deep:#1688c9;
    --blue-band:#1c9ad3;
    --logo-blue:#1aa3de;
    --orange:#f5a623;
    --text-white:#ffffff;
  }
  html,body{margin:0;padding:0;width:1200px;height:892px;overflow:hidden;background:var(--page);}
  .canvas{position:relative;width:1200px;height:892px;}
  .card{
    position:absolute;left:75px;top:146px;width:1050px;height:600px;
    background:var(--card-white);overflow:hidden;
    box-shadow:0 10px 30px rgba(0,0,0,.18);
  }
  .card__panel{position:absolute;inset:0;}
  .brand{
    position:absolute;left:70px;top:250px;width:400px;
    display:flex;align-items:center;gap:16px;
  }
  .brand__dot{width:34px;height:34px;border-radius:50%;background:var(--logo-blue);flex:none;}
  .brand__name{
    font-family:"Arimo",sans-serif;font-weight:700;font-size:38px;
    color:var(--logo-blue);line-height:1.1;
  }
  .holder{
    position:absolute;left:560px;top:36px;width:460px;
    font-family:"Playfair Display",serif;font-weight:700;font-size:44px;
    color:var(--text-white);text-align:right;letter-spacing:.5px;
  }
  .contacts{
    position:absolute;right:40px;top:250px;list-style:none;margin:0;padding:0;
    font-family:"Arimo",sans-serif;font-size:24px;color:var(--text-white);
  }
  .contacts__item{display:flex;justify-content:flex-end;align-items:center;gap:18px;height:54px;}
  .contacts__icon{width:26px;height:26px;flex:none;}
</style>
</head>
<body>
<div class="canvas">
  <div class="card">
    <svg class="card__panel" width="1050" height="600" viewBox="0 0 1050 600" aria-hidden="true">
      <defs>
        <linearGradient id="band" x1="0" y1="0" x2="1" y2="0">
          <stop offset="0" stop-color="#3cc2ea"/>
          <stop offset=".5" stop-color="#62d3f1"/>
          <stop offset="1" stop-color="#2aa8dd"/>
        </linearGradient>
        <linearGradient id="body" x1="0" y1="0" x2="1" y2="1">
          <stop offset="0" stop-color="#2fb3e3"/>
          <stop offset="1" stop-color="#1585c6"/>
        </linearGradient>
      </defs>
      <polygon points="480,0 1050,0 1050,600 480,600 640,300" fill="url(#body)"/>
      <polygon points="480,0 1050,0 1050,140 560,140" fill="url(#band)"/>
      <line x1="560" y1="140" x2="1050" y2="140" stroke="#1790cf" stroke-width="3"/>
      <polyline points="480,0 640,300 480,600" fill="none" stroke="var(--blue-deep)" stroke-width="4"/>
    </svg>

    <div class="brand">
      <span class="brand__dot"></span>
      <span class="brand__name">Tall Pine Computing</span>
    </div>

    <div class="holder">Owen Hartley Reese</div>

    <ul class="contacts">
      <li class="contacts__item"><span>1300 555 019</span>
        <svg class="contacts__icon" viewBox="0 0 26 26"><rect width="26" height="26" rx="3" fill="#fff"/><path d="M8 6h4l1 4-2 1.5a9 9 0 0 0 4 4L16.5 13l4 1v4c-7 1-13-5-12.5-12z" fill="var(--blue-deep)"/></svg></li>
      <li class="contacts__item"><span>info@tallpinecomputing.com.au</span>
        <svg class="contacts__icon" viewBox="0 0 26 26"><rect width="26" height="26" rx="3" fill="#fff"/><rect x="5" y="8" width="16" height="11" fill="none" stroke="var(--blue-deep)" stroke-width="2"/><path d="M5 8l8 6 8-6" fill="none" stroke="var(--blue-deep)" stroke-width="2"/></svg></li>
      <li class="contacts__item"><span>www.tallpinecomputing.com</span>
        <svg class="contacts__icon" viewBox="0 0 26 26"><rect width="26" height="26" rx="3" fill="#fff"/><circle cx="13" cy="13" r="7.5" fill="none" stroke="var(--blue-deep)" stroke-width="2"/><path d="M5.5 13h15M13 5.5c-4 5-4 10 0 15M13 5.5c4 5 4 10 0 15" fill="none" stroke="var(--blue-deep)" stroke-width="1.5"/></svg></li>
      <li class="contacts__item"><span>4120 Cedarbank Road Fernhill,BC</span>
        <svg class="contacts__icon" viewBox="0 0 26 26"><rect width="26" height="26" rx="3" fill="#fff"/><path d="M13 21s-6-6.5-6-10.5a6 6 0 0 1 12 0C19 14.5 13 21 13 21z" fill="var(--blue-deep)"/><circle cx="13" cy="10.5" r="2.2" fill="#fff"/></svg></li>
    </ul>
  </div>
</div>
</body>
</html>
```